Design my dad a new business card because his current one sucks!

I need a business card designed for my fathers home maintenance business. His customers are individuals (single moms, old people etc.) as well as the occasional business. As such it needs to be accessible to both target audiences.

The front of the card should be dark grey on yellow with the logo and contain the following information:
- Darren Holtwick
- 0488 274 915
- info@brightoakhomecare.com.au
- 0488 274 915

- ABN: 71 284 630 912
- 'Fully Insured'

The reverse should be yellow on dark grey and will have the web address:
- brightoakhomecare.com.au

And a few key services he offers:
GENERAL REPAIRS
PAINTING/TILING/
PAVING &CONCRETING
PRESSURE WASHING
ON-SITE WELDING
DECKING ADDITIONS & REPAIRS
FENCING
FULL BOND CLEANING

This will be first time the logo has been printed so you will need to come up with the best CMYK approximation of the RGB colours to make sure it is a close as possible.

```html
<!DOCTYPE html>
<html lang="en">
<head>
<meta charset="utf-8">
<title>Bright Oak Home Care – Services</title>
<link href="https://fonts.googleapis.com/css2?family=Open+Sans:wght@400;600&display=swap" rel="stylesheet">
<style>
  :root {
    --card-dark: #5f5c5b;
    --card-mid: #6b6968;
    --card-light: #8a8988;
    --service-yellow: #f4f400;
    --mark-tone: rgba(70, 66, 64, 0.35);
  }
  html, body {
    margin: 0;
    padding: 0;
    width: 1200px;
    height: 686px;
    overflow: hidden;
    background: var(--card-dark);
  }
  .card-back {
    position: relative;
    width: 1200px;
    height: 686px;
    overflow: hidden;
    background:
      radial-gradient(ellipse 520px 420px at 430px 300px, rgba(140,139,138,0.55), rgba(140,139,138,0) 70%),
      linear-gradient(100deg, var(--card-mid) 0%, var(--card-light) 40%, var(--card-dark) 75%, #5a5756 100%);
    font-family: "Open Sans", Arial, sans-serif;
  }
  .brand-backdrop {
    position: absolute;
    left: 500px;
    top: 0;
    width: 560px;
    height: 686px;
    background: linear-gradient(160deg, rgba(95,92,91,0.35), rgba(95,92,91,0.15));
    clip-path: polygon(30% 0, 100% 0, 100% 100%, 10% 100%, 0 60%, 12% 30%);
  }
  .brand-mark {
    position: absolute;
    left: 520px;
    top: 360px;
    transform-origin: 0 0;
    transform: rotate(-28deg);
    color: var(--mark-tone);
    font-weight: 600;
    font-size: 88px;
    line-height: 1;
    white-space: nowrap;
    letter-spacing: 2px;
  }
  .service {
    position: absolute;
    margin: 0;
    color: var(--service-yellow);
    font-weight: 400;
    font-size: 33px;
    line-height: 1;
    white-space: nowrap;
    transform-origin: 0 100%;
    transform: rotate(-28.5deg);
  }
  .service--general  { left: 62px;  top: 160px; }
  .service--tiling   { left: 480px; top: 75px; }
  .service--paving   { left: 46px;  top: 318px; }
  .service--pressure { left: 346px; top: 322px; }
  .service--welding  { left: 816px; top: 228px; }
  .service--bond     { left: 796px; top: 412px; }
  .service--painting { left: 112px; top: 456px; }
  .service--decking  { left: 252px; top: 548px; }
  .service--fencing  { left: 508px; top: 574px; }
</style>
</head>
<body>
  <main class="card-back">
    <div class="brand-backdrop" role="img" aria-label="Soft lighter grey paint-stroke backdrop"></div>
    <div class="brand-mark" aria-hidden="true">Bright Oak Home Care</div>

    <p class="service service--general">GENERAL REPAIRS</p>
    <p class="service service--tiling">TILING</p>
    <p class="service service--paving">PAVING &amp;CONCRETING</p>
    <p class="service service--pressure">PRESSURE WASHING</p>
    <p class="service service--welding">ON-SITE WELDING</p>
    <p class="service service--bond">FULL BOND CLEANING</p>
    <p class="service service--painting">PAINTING</p>
    <p class="service service--decking">DECKING ADDITIONS &amp; REPAIRS</p>
    <p class="service service--fencing">FENCING</p>
  </main>
</body>
</html>
```